Social Media App Needs PPT Template

We need a PowerPoint template for a new social media company based in the DC area called "Bold Ledger." We provide an interactive digital platform for executives to share actionable advice. We would like to see designs that use our orange logo color as an accent, but are mainly grey, white, and black. The final design should communicate clean, chic, modern, and professional.

Target Market(s)

Executives

Industry/Entity Type

Information Technology

Font styles to use
Sans Serif

Colors
f78f20
fbe7d2
ffffff
000000
e8e8e8
757575

Requirements
Must have
• My project must have title page and many options for the body of the ppt (graphs, tables, etc). It also needs to be easy to modify. I must have someone who is experienced in creating powerpoint templates.
Nice to have
• It would be nice to have a very modern and clean design that includes the logo on every page, but still leaves a lot of room for the content of the slide
Should not have
• My design project should not look to busy.

```html
<!DOCTYPE html>
<html lang="en">
<head>
<meta charset="utf-8">
<title>Bold Ledger – About Our Company</title>
<link rel="stylesheet" href="https://fonts.googleapis.com/css2?family=Lato:wght@300;400;700&display=swap">
<style>
  :root {
    --orange: #ea8419;
    --orange-bright: #f0901e;
    --navy: #232d3c;
    --charcoal: #555759;
    --silver: #cccdce;
    --heading-grey: #4a4b4d;
    --body-grey: #7a7a7a;
    --footer-text: #d6d9de;
    --backdrop: #555555;
    --white: #ffffff;
  }
  * { margin: 0; padding: 0; box-sizing: border-box; }
  html, body {
    width: 1200px; height: 960px; overflow: hidden;
    background: var(--backdrop);
    font-family: "Lato", Arial, sans-serif;
  }
  .canvas { position: relative; width: 1200px; height: 960px; }
  .slide {
    position: absolute; left: 0; top: 29px;
    width: 1212px; height: 910px;
    transform: scale(0.9901); transform-origin: 0 0;
    background: radial-gradient(ellipse at 50% 35%, #ffffff 0%, #f7f7f7 55%, #efefef 100%);
    overflow: hidden;
  }
  .slide-art { position: absolute; left: 0; top: 0; }
  .slide-title {
    position: absolute; left: 37px; top: 80px;
    font-weight: 300; font-size: 46px; color: var(--white); letter-spacing: 0.2px;
  }
  .brand {
    position: absolute; left: 985px; top: 86px;
    display: flex; align-items: center; gap: 10px;
    font-weight: 700; font-size: 27px; color: var(--white);
  }
  .brand-dot { width: 22px; height: 22px; border-radius: 50%; background: var(--orange-bright); }
  .point { position: absolute; width: 300px; }
  .point-heading {
    font-weight: 700; font-size: 28px; line-height: 1; letter-spacing: -0.2px;
    margin-bottom: 20px; white-space: nowrap;
  }
  .point-text { font-size: 20px; line-height: 29px; color: var(--body-grey); }
  .point--charcoal { left: 101px; top: 264px; }
  .point--charcoal .point-heading { color: var(--heading-grey); }
  .point--orange { left: 802px; top: 264px; }
  .point--orange .point-heading { color: var(--orange-bright); }
  .point--navy { left: 101px; top: 571px; }
  .point--navy .point-heading { color: var(--navy); }
  .point--silver { left: 814px; top: 571px; }
  .point--silver .point-heading { color: var(--silver); }
  .share {
    position: absolute; font-size: 24px; color: var(--white);
    transform: translate(-50%, -50%);
  }
  .footer-text {
    position: absolute; left: 33px; top: 868px;
    font-size: 16px; color: var(--footer-text);
  }
  .footer-text .divider { margin: 0 6px; }
</style>
</head>
<body>
<div class="canvas">
  <section class="slide">
    <svg class="slide-art" width="1212" height="910" viewBox="0 0 1212 910">
      <!-- header -->
      <polygon points="0,57 1060,57 965,152 0,152" fill="var(--orange)"/>
      <polygon points="730,57 870,57 790,133 660,133" fill="#ef8d20" opacity="0.6"/>
      <polygon points="0,133 800,133 780,152 0,152" fill="#e37c14" opacity="0.5"/>
      <polygon points="1068,57 1212,57 1212,152 972,152" fill="var(--navy)"/>
      <polygon points="1082,41 1212,41 1212,52 1071,52" fill="var(--orange)"/>
      <polygon points="0,155 958,155 944,169 0,169" fill="var(--navy)"/>
      <!-- connector lines -->
      <polyline points="95,300 450,300 521,382" fill="none" stroke="var(--heading-grey)" stroke-width="2"/>
      <polyline points="1090,300 745,300 674,382" fill="none" stroke="var(--orange-bright)" stroke-width="2"/>
      <polyline points="95,607 441,607 477,564" fill="none" stroke="var(--navy)" stroke-width="2"/>
      <polyline points="1100,607 755,607 712,573" fill="none" stroke="var(--silver)" stroke-width="2"/>
      <!-- donut chart -->
      <g stroke="#ffffff" stroke-width="2">
        <path d="M597,361 A137,137 0 0 1 734,498 L660,498 A63,63 0 0 0 597,435 Z" fill="var(--orange-bright)"/>
        <path d="M734,498 A137,137 0 0 1 597,635 L597,561 A63,63 0 0 0 660,498 Z" fill="var(--silver)"/>
        <path d="M597,635 A137,137 0 0 1 460,498 L534,498 A63,63 0 0 0 597,561 Z" fill="var(--navy)"/>
        <path d="M460,498 A137,137 0 0 1 597,361 L597,435 A63,63 0 0 0 534,498 Z" fill="var(--charcoal)"/>
      </g>
      <!-- footer -->
      <polygon points="0,861 345,861 309,896 0,896" fill="var(--navy)"/>
      <polygon points="352,861 1212,861 1212,896 316,896" fill="var(--orange)"/>
    </svg>

    <h1 class="slide-title">About Our Company</h1>
    <div class="brand"><span class="brand-dot"></span>Bold Ledger</div>

    <span class="share" style="left:530px; top:432px;">25%</span>
    <span class="share" style="left:669px; top:432px;">25%</span>
    <span class="share" style="left:530px; top:570px;">25%</span>
    <span class="share" style="left:669px; top:570px;">25%</span>

    <div class="point point--charcoal">
      <h2 class="point-heading">NOBIS VIDENTUR</h2>
      <p class="point-text">Lorem ipsum dolor sit amet, consectetuer adipi scing elit, sed diam nonummy nibh euismod tin.</p>
    </div>
    <div class="point point--orange">
      <h2 class="point-heading">NOBIS VIDENTUR</h2>
      <p class="point-text">Lorem ipsum dolor sit amet, consectetuer adipi scing elit, sed diam nonummy nibh euismod tin.</p>
    </div>
    <div class="point point--navy">
      <h2 class="point-heading">NOBIS VIDENTUR</h2>
      <p class="point-text">Lorem ipsum dolor sit amet, consectetuer adipi scing elit, sed diam nonummy nibh euismod tin.</p>
    </div>
    <div class="point point--silver">
      <h2 class="point-heading">NOBIS VIDENTUR</h2>
      <p class="point-text">Lorem ipsum dolor sit amet, consectetuer adipi scing elit, sed diam nonummy nibh euismod tin.</p>
    </div>

    <p class="footer-text">www.boldledger.com<span class="divider">|</span>Page 6</p>
  </section>
</div>
</body>
</html>
```